Holistic Health Coach needs simple web site design for a new practice

I need a web (re)design for my entire site, Ridgeway Fern Lady. I have a beautiful new blue and green logo that I'd like the site fonts and color scheme to be built around. I'll attach my new logo so you'll know the colors/design feel I'm after.

I want easy navigation for my mostly text based site, widgets for my social media pages and a clean, fun, light feel for the site.

Target Market(s)

People looking to take charge of their own health, and who may need my coaching services to obtain optimal wellness.

Industry/Entity Type

Health

Coding

Coded - Design and coding required

Number of Pages Required

5+ page

Font styles to use
Script

Colors
33b8a4
33a6d7
ffffff

Requirements
Must have
• Must incorporate my logo design, as well as same/similar fonts and color scheme.
• I'd like it to stay as close to the current design as possible.
Nice to have
• Would love to incorporate a hover over menu (for example, when a user hovers over "About", they will see the submenu in a floating design.
Should not have
• No dark colors or masculine feel

```html
<!DOCTYPE html>
<html lang="en">
<head>
<meta charset="utf-8">
<title>Ridgeway Fern Lady</title>
<link href="https://fonts.googleapis.com/css2?family=Ubuntu:wght@400;500;700&family=Arimo:wght@400;700&display=swap" rel="stylesheet">
<style>
:root{
  --teal:#33b8a4;
  --teal-dark:#2fae9c;
  --blue:#33a6d7;
  --blue-deep:#2a8fc4;
  --white:#ffffff;
  --text:#666b70;
  --meta:#8a8f94;
  --line:#e3e6e8;
  --btn:#eeeff0;
  --dark-btn:#4d5358;
}
*{box-sizing:border-box;margin:0;padding:0}
html,body{width:1200px;height:2166px;overflow:hidden;background:var(--white)}
body{position:relative;font-family:'Arimo',Arial,sans-serif;color:var(--text)}
.abs{position:absolute}
.topline{left:0;top:0;width:1200px;height:3px;background:#8cc63f}
.header{left:0;top:3px;width:1200px;height:78px;background:linear-gradient(#fff,#f4f5f6);border-bottom:1px solid var(--line)}
.logo{left:126px;top:32px;font-family:'Ubuntu',sans-serif;font-size:21px;font-weight:500;color:var(--teal);display:flex;align-items:center;gap:8px;white-space:nowrap}
.logo i{display:block;width:12px;height:12px;border-radius:50%;background:var(--blue)}
.nav{font-family:'Ubuntu',sans-serif;font-size:13.5px;font-weight:500;color:#333;top:38px;white-space:nowrap}
.nav-about{left:478px;top:14px;width:107px;height:67px;background:#eef6fb;border-top:3px solid var(--blue);color:var(--blue);text-align:center;padding-top:21px}
.dropdown{left:478px;top:81px;width:172px;height:120px;background:#fff;box-shadow:0 2px 6px rgba(0,0,0,.15);font-family:'Ubuntu',sans-serif;font-size:13px;color:#333}
.dropdown div{height:38px;line-height:38px;padding-left:21px;border-bottom:1px solid #eee}
.dropdown .active{background:#eef6fb;color:var(--blue);border-top:2px solid var(--blue)}
.band{left:0;top:243px;width:1200px;height:140px;background:var(--teal)}
.hero{left:100px;top:92px;width:1000px;height:428px;background:var(--blue);border-radius:3px;overflow:hidden}
.skyline{left:0;top:170px;width:1000px;height:258px;background:linear-gradient(#3aaee0,#2b9fd2)}
.hero-icon{left:432px;top:105px;width:136px;height:125px;border-radius:50%;background:rgba(255,255,255,.25)}
.arrow{width:34px;height:34px;display:flex;align-items:center;justify-content:center}
.hero h1{left:0;width:1000px;top:226px;text-align:center;font-family:'Ubuntu',sans-serif;font-weight:400;font-size:32px;color:#fff}
.hero p{left:230px;width:540px;top:278px;text-align:center;font-size:13px;line-height:19px;color:#eaf6fc}
.hero-btn{left:423px;top:327px;width:153px;height:39px;background:#3fbbee;border-radius:2px;color:#fff;font-family:'Ubuntu',sans-serif;font-weight:700;font-size:14px;display:flex}
.hero-btn span{flex:1;line-height:39px;text-align:center}
.hero-btn b{width:38px;background:var(--blue-deep);display:flex;align-items:center;justify-content:center}
.post-title{left:115px;width:620px;font-family:'Ubuntu',sans-serif;font-weight:500;font-size:19px;line-height:25px;color:var(--teal-dark)}
.meta{left:116px;font-size:10.5px;color:var(--meta);white-space:nowrap}
.meta b{color:#666}
.post-img{left:111px;width:689px;border-radius:2px}
.excerpt{left:116px;width:685px;font-size:10.4px;line-height:13.5px;color:#7a7f84}
.actions{left:114px;display:flex;gap:6px;align-items:center;font-size:10.5px;color:#777;white-space:nowrap}
.comment{width:129px;height:26px;line-height:26px;background:var(--btn);border-radius:2px;text-align:center;margin-right:12px}
.share{height:22px;line-height:22px;padding:0 7px;background:#f6f7f8;border-radius:2px}
.share i{display:inline-block;width:8px;height:8px;background:#888;margin-right:5px;vertical-align:middle;border-radius:1px}
.count{display:inline-block;width:11px;height:11px;border-radius:50%;background:var(--blue);color:#fff;font-size:8px;line-height:11px;text-align:center;margin-left:3px}
.read{left:117px;width:74px;height:22px;line-height:22px;background:var(--blue);color:#fff;font-size:10px;font-weight:700;text-align:center;border-radius:2px}
.pager{top:1812px;height:22px;width:28px;line-height:22px;text-align:center;font-size:11px;border-radius:2px;background:#eef0f1;color:#888}
.side-h{left:846px;width:234px;font-family:'Ubuntu',sans-serif;font-size:17px;color:#555;padding-bottom:6px;border-bottom:1px solid var(--line)}
.search{left:846px;top:618px;width:230px;height:23px;border:1px solid #ddd;font-size:10px;color:#aaa;line-height:21px;padding-left:9px}
.ad{width:107px;height:107px;border:1px solid #ddd}
.ad-grey{background:#d5d6d7;display:flex;flex-direction:column;align-items:center;justify-content:center;color:#fff;font-family:'Ubuntu',sans-serif;font-size:24px}
.ad-grey small{display:block;margin-top:4px;background:#9a9c9e;font-size:10px;padding:2px 14px}
.thumb{width:65px;height:65px;border:1px solid #ddd;padding:3px}
.thumb span{display:block;width:100%;height:100%}
.footer{left:0;top:1880px;width:1200px;height:226px;background:var(--teal);color:#fff}
.f-h{font-family:'Ubuntu',sans-serif;font-size:16px;top:46px}
.f-t{font-size:9.3px;line-height:15px;font-weight:700}
.f-list div{height:26px;line-height:26px;border-bottom:1px solid rgba(255,255,255,.35);font-size:9.3px;font-weight:700;padding-left:12px}
.bottom{left:0;top:2106px;width:1200px;height:60px;background:var(--blue);color:#fff}
.sq{top:14px;width:32px;height:32px;border-radius:2px}
</style>
</head>
<body>
<div class="abs topline"></div>
<header class="abs header"></header>
<div class="abs logo"><i></i>Ridgeway Fern Lady</div>
<div class="abs nav" style="left:409px">Home</div>
<div class="abs nav nav-about">About Dana</div>
<div class="abs nav" style="left:598px">Article</div>
<div class="abs nav" style="left:665px">Essential Oils</div>
<div class="abs nav" style="left:770px">21-Day Clean Slate Coaching Services</div>

<div class="abs band"></div>
<section class="abs hero">
  <div class="abs skyline" role="img" aria-label="Faint city skyline illustration"></div>
  <div class="abs hero-icon" role="img" aria-label="White apple icon with a cross"></div>
  <div class="abs arrow" style="left:106px;top:197px;background:#1f6fa8"><svg width="10" height="12"><path d="M8 1 3 6l5 5" stroke="#fff" stroke-width="2" fill="none"/></svg></div>
  <div class="abs arrow" style="left:862px;top:197px;background:var(--teal)"><svg width="10" height="12"><path d="M2 1l5 5-5 5" stroke="#fff" stroke-width="2" fill="none"/></svg></div>
  <h1 class="abs">Module 4 of Root Reset</h1>
  <p class="abs">Lorem ipsum dolor sit amet, consectetur adipisicing elit, sed do eiusmod tempor incididunt ut labore et dolore magna aliqua.</p>
  <div class="abs hero-btn"><span>More Details</span><b><svg width="10" height="14"><path d="M2 1l6 6-6 6" stroke="#fff" stroke-width="2.2" fill="none"/></svg></b></div>
</section>
<nav class="abs dropdown">
  <div>Image Gallery</div>
  <div class="active">Portfolio</div>
  <div>Statistics</div>
</nav>

<!-- Post 1 -->
<h2 class="abs post-title" style="top:537px">Lifestyles of the Tired and Wired – Module 4 of Root Reset:<br>Adrenal Fatigue</h2>
<div class="abs meta" style="top:599px">08.08.2015 &nbsp;/&nbsp; In <b>Tutorials</b> &nbsp;/&nbsp; by <b>Template Hollow</b> &nbsp;/&nbsp; with &nbsp;08 &nbsp;Comments</div>
<div class="abs post-img" style="top:622px;height:157px;background:#e8703a" role="img" aria-label="Orange banner with a round white emblem"></div>
<p class="abs excerpt" style="top:795px">Ut lobortis sodales diam euismod venenatis. Suspendisse at turpis in purus suscipit tincidunt. Sed bibendum neque eu justo malesuada eget sagittis lorem dictum. Quisque vehicula, justo eu sollicitudin tincidunt, libero nisl varius leo, id tempor nisl justo ac arcu.facilisis nisi, non luctus nunc suscipit vel.eros.</p>
<div class="abs actions" style="top:852px"><span class="comment">Leave Your Comment »</span><span class="share"><i></i>Email</span><span class="share"><i></i>Print</span><span class="share"><i></i>Circlebook</span><span class="share"><i></i>Chirper<span class="count">2</span></span><span class="share"><i></i>Searchly</span><span class="share"><i></i>Pinboard</span></div>
<div class="abs read" style="top:897px">Read More</div>

<!-- Post 2 -->
<h2 class="abs post-title" style="top:928px">April Wellness Living Class Series</h2>
<div class="abs meta" style="top:969px">08.08.2015 &nbsp;/&nbsp; In <b>Tutorials</b> &nbsp;/&nbsp; by <b>Template Hollow</b> &nbsp;/&nbsp; with &nbsp;08 &nbsp;Comments</div>
<div class="abs post-img" style="top:995px;height:156px;background:#f4b8bd" role="img" aria-label="Pink schedule graphic with hand-lettered class dates"></div>
<p class="abs excerpt" style="top:1181px">Ut lobortis sodales diam euismod venenatis. Suspendisse at turpis in purus suscipit tincidunt. Sed bibendum neque eu justo malesuada eget sagittis lorem dictum. Quisque vehicula, justo eu sollicitudin tincidunt, libero nisl varius leo, id tempor nisl justo ac arcu.facilisis nisi, non luctus nunc suscipit vel.eros.</p>
<div class="abs actions" style="top:1239px"><span class="comment">Leave Your Comment »</span><span class="share"><i></i>Email</span><span class="share"><i></i>Print</span><span class="share"><i></i>Circlebook</span><span class="share"><i></i>Chirper<span class="count">2</span></span><span class="share"><i></i>Searchly</span><span class="share"><i></i>Pinboard</span></div>
<div class="abs read" style="top:1284px">Read More</div>

<!-- Post 3 -->
<h2 class="abs post-title" style="top:1338px">What Do You Mean I Can’t Have Coffee?!? – Module 2 Root Reset:<br>Adrenal Fatigue</h2>
<div class="abs meta" style="top:1399px">08.08.2015 &nbsp;/&nbsp; In <b>Tutorials</b> &nbsp;/&nbsp; by <b>Template Hollow</b> &nbsp;/&nbsp; with &nbsp;08 &nbsp;Comments</div>
<div class="abs post-img" style="top:1425px;height:182px;border:1px solid #ddd"></div>
<div class="abs" style="left:312px;top:1435px;width:245px;height:164px;background:linear-gradient(#e9e2d4,#9fbfc4)" role="img" aria-label="Herbal coffee blend promo with a cup of coffee"></div>
<p class="abs excerpt" style="top:1632px">Ut lobortis sodales diam euismod venenatis. Suspendisse at turpis in purus suscipit tincidunt. Sed bibendum neque eu justo malesuada eget sagittis lorem dictum. Quisque vehicula, justo eu sollicitudin tincidunt, libero nisl varius leo, id tempor nisl justo ac arcu.facilisis nisi, non luctus nunc suscipit vel.eros.</p>
<div class="abs actions" style="top:1695px"><span class="comment">Leave Your Comment »</span><span class="share"><i></i>Email</span><span class="share"><i></i>Print</span><span class="share"><i></i>Circlebook</span><span class="share"><i></i>Chirper<span class="count">2</span></span><span class="share"><i></i>Searchly</span><span class="share"><i></i>Pinboard</span></div>
<div class="abs read" style="top:1739px">Read More</div>

<div class="abs pager" style="left:121px;background:var(--dark-btn);color:#fff">1</div>
<div class="abs pager" style="left:157px">2</div>
<div class="abs pager" style="left:193px">»</div>
<div class="abs meta" style="left:553px;top:1817px">Page 1 of 2</div>

<!-- Sidebar -->
<div class="abs side-h" style="top:533px">Subscribe here now!</div>
<div class="abs" style="left:1054px;top:535px;width:22px;height:22px;border-radius:50%;background:#9b9ea1"></div>
<div class="abs side-h" style="top:575px">Search:</div>
<div class="abs search">Search our site</div>
<div class="abs side-h" style="top:661px">Advertise:</div>
<div class="abs ad" style="left:846px;top:706px;background:linear-gradient(#fff,#f1eef6)" role="img" aria-label="Website template advertisement"></div>
<div class="abs ad" style="left:969px;top:706px;background:linear-gradient(#fff,#e9dff0)" role="img" aria-label="Web template advertisement"></div>
<div class="abs ad" style="left:846px;top:827px;background:linear-gradient(#fff,#f4f1de)" role="img" aria-label="Theme advertisement"></div>
<div class="abs ad ad-grey" style="left:969px;top:827px">Ads<small>advertise</small></div>
<div class="abs" style="left:846px;width:230px;top:954px;text-align:center;font-size:9.5px;color:#555">Learn More About Advertising Here</div>
<div class="abs" style="left:845px;top:1009px;font-family:'Ubuntu',sans-serif;font-size:14.5px;color:#444">RIDGEWAY FERN LADY ON SNAPGRAM</div>
<div class="abs thumb" style="left:847px;top:1047px"><span style="background:#c9a6cf" role="img" aria-label="Flower photo"></span></div>
<div class="abs thumb" style="left:929px;top:1047px"><span style="background:#9fa86a" role="img" aria-label="Portrait photo"></span></div>
<div class="abs thumb" style="left:1011px;top:1047px"><span style="background:#5a5152" role="img" aria-label="Portrait photo"></span></div>
<div class="abs thumb" style="left:847px;top:1126px"><span style="background:#8fb2c8" role="img" aria-label="Beach photo"></span></div>
<div class="abs thumb" style="left:929px;top:1126px"><span style="background:#c9704f" role="img" aria-label="Rose photo"></span></div>
<div class="abs thumb" style="left:1011px;top:1126px"><span style="background:#d6a53a" role="img" aria-label="Bird photo"></span></div>
<div class="abs thumb" style="left:847px;top:1204px"><span style="background:#8c9a3f" role="img" aria-label="Cup and flower photo"></span></div>
<div class="abs thumb" style="left:929px;top:1204px"><span style="background:#a899b8" role="img" aria-label="Flower photo"></span></div>
<div class="abs thumb" style="left:1011px;top:1204px"><span style="background:#3f8a8a" role="img" aria-label="Portrait photo"></span></div>
<div class="abs" style="left:860px;top:1295px;font-size:10px;color:#444"><span style="display:inline-block;width:14px;height:7px;border-radius:4px;background:#555;margin-right:10px"></span>Load more</div>
<div class="abs" style="left:940px;top:1289px;width:116px;height:22px;line-height:22px;background:var(--teal);color:#fff;font-size:9.5px;text-align:center">Follow on Snapgram</div>
<div class="abs" style="left:853px;top:1333px;width:216px;height:198px;border:1px solid #ddd;background:#d5d6d7"></div>
<div class="abs" style="left:854px;top:1334px;width:214px;height:80px;background:#fff;padding:8px 6px;font-family:'Ubuntu',sans-serif;color:#1e4f86">
  <div style="font-size:18px;font-weight:700"><span style="color:var(--blue)">6,000+</span> Web Templates</div>
  <div style="font-size:13px;margin-top:3px"><u>Unlimited</u> Downloads for $59.95</div>
  <div style="font-size:6.5px;color:#777;margin-top:6px">NO PER PRODUCT FEES &nbsp; ONE FULL YEAR SUBSCRIPTION</div>
</div>
<div class="abs ad-grey" style="left:854px;top:1414px;width:214px;height:116px;display:flex">Ads<small>advertise</small></div>

<!-- Footer -->
<footer class="abs footer">
  <div class="abs f-h" style="left:134px">Lorem ipsum</div>
  <div class="abs f-t" style="left:134px;top:68px;width:255px">Lorem ipsum dolor sit amet, consectetur adipisicing elit, sed do eiusmod tempor</div>
  <div class="abs f-t" style="left:134px;top:107px;width:255px">Lorem Ipsum is simply dummy text of the printing and typesetting industry. Lorem Ipsum has been the industry's standard dummy text &nbsp;<u>Read More</u></div>
  <div class="abs f-h" style="left:498px">Recent posts</div>
  <div class="abs f-t" style="left:498px;top:68px;width:210px">Lorem ipsum dolor sit amet, consectetur adipis-icing elit, sed do eiusmod tempor</div>
  <div class="abs f-list" style="left:492px;top:100px;width:215px">
    <div>• Consectetur adipisicing elit</div>
    <div>• Sed do eiusmod tempor incididunt</div>
    <div>• Rabore et dolore magna aliqua</div>
    <div style="border:none">• Ut enim ad minim veniam</div>
  </div>
  <div class="abs f-h" style="left:774px">Recent posts</div>
  <div class="abs f-t" style="left:774px;top:68px;width:315px">Lorem ipsum dolor sit amet, consectetur adipisicing elit, sed do eiusmod tempor</div>
  <div class="abs f-t" style="left:774px;top:107px;width:315px">Lorem Ipsum is simply dummy text of the printing and typesetting industry. Lorem Ipsum has been the industry's standard dummy text ever since the 1500s, when an unknown printer took a galley of type and scrambled it to make &nbsp;<u>Read More</u></div>
</footer>
<div class="abs bottom">
  <div class="abs" style="left:128px;top:27px;font-size:10.5px">© Copyright <b>SiteName</b>. All Rights Reserved.</div>
  <div class="abs sq" style="left:871px;background:#6a5bab"></div>
  <div class="abs sq" style="left:908px;background:#4ec1ee"></div>
  <div class="abs sq" style="left:947px;background:#d6434a"></div>
  <div class="abs sq" style="left:988px;background:#f78b1e"></div>
  <div class="abs sq" style="left:1064px;background:#2688c0;display:flex;align-items:center;justify-content:center"><svg width="12" height="8"><path d="M1 7l5-5 5 5" stroke="#fff" stroke-width="2" fill="none"/></svg></div>
</div>
</body>
</html>
```